Ward Compass Business Card Design*

We need a business card design for our company Ward Compass. Our company is specialized in providing online consulting services regarding medical institutions, hospitals and doctors. We work with patients worldwide looking to choose between healthcare providers. We have a website you may use as a reference, where we list doctors and clinics worldwide. So we target Medical providers as well as patients worldwide.
Target Market(s)
Medical Providers and patients around the world
Industry/Entity Type
Medical
Contact Information for Business Card
Salwa Kettani
CEO
+90 612 348 2175
info@wardcompass.example
www.wardcompass.example
14 Annakhil 7 H.R.B. Rabat, Morocco
Requirements
Must have
- Company logo/name on one full side, personal info and smaller logo and company name on the other side.
Nice to have
- Smart and elegant design

```html
<!DOCTYPE html>
<html lang="en">
<head>
<meta charset="utf-8">
<title>Ward Compass — Business Card</title>
<link rel="stylesheet" href="https://fonts.googleapis.com/css2?family=Montserrat:wght@300;600&family=Open+Sans:wght@400;700&display=swap">
<style>
  :root {
    --navy: #1d3f6e;
    --grey: #7a7a7a;
    --ink: #2b2b2b;
    --paper: #ffffff;
    --backdrop: #e9eaec;
    --rule: #9bb0cc;
  }
  * { box-sizing: border-box; margin: 0; padding: 0; }
  html, body { width: 1200px; height: 768px; overflow: hidden; }
  body {
    background: var(--backdrop);
    display: flex;
    align-items: center;
    justify-content: center;
    gap: 40px;
    font-family: "Open Sans", Arial, sans-serif;
  }
  .card {
    width: 540px;
    height: 309px;
    background: var(--paper);
    box-shadow: 0 6px 18px rgba(0,0,0,0.12);
    position: relative;
  }
  /* Brand side */
  .card--brand {
    display: flex;
    flex-direction: column;
    align-items: center;
    justify-content: center;
  }
  .brand-lockup {
    display: flex;
    align-items: center;
    gap: 14px;
  }
  .brand-dot {
    width: 34px; height: 34px;
    border-radius: 50%;
    background: var(--navy);
  }
  .brand-name {
    font-family: "Montserrat", Arial, sans-serif;
    font-weight: 600;
    font-size: 28px;
    letter-spacing: 2px;
    text-transform: uppercase;
    color: var(--navy);
  }
  .brand-web {
    position: absolute;
    bottom: 34px;
    left: 0; right: 0;
    text-align: center;
    font-family: "Montserrat", Arial, sans-serif;
    font-weight: 300;
    font-size: 12px;
    letter-spacing: 5px;
    color: var(--ink);
  }
  /* Contact side */
  .card--contact {
    display: flex;
    align-items: center;
    padding: 0 40px 0 46px;
  }
  .contact-mark {
    width: 170px;
    display: flex;
    flex-direction: column;
    align-items: center;
    gap: 12px;
  }
  .contact-mark .brand-dot { width: 70px; height: 70px; }
  .contact-mark .brand-name { font-size: 17px; letter-spacing: 1.5px; }
  .contact-rule {
    width: 1px;
    height: 150px;
    background: var(--rule);
    margin: 0 18px 0 14px;
  }
  .contact-info { font-size: 13px; line-height: 1.35; color: var(--ink); }
  .person-name { font-weight: 700; font-size: 19px; color: var(--navy); line-height: 1.1; }
  .person-role { color: var(--grey); font-size: 13px; margin-bottom: 10px; }
  .address { margin-bottom: 2px; }
  .contact-line .label { font-weight: 700; color: var(--navy); margin-right: 4px; }
</style>
</head>
<body>
  <section class="card card--brand">
    <div class="brand-lockup">
      <span class="brand-dot"></span>
      <span class="brand-name">Ward Compass</span>
    </div>
    <p class="brand-web">www.wardcompass.example</p>
  </section>

  <section class="card card--contact">
    <div class="contact-mark">
      <span class="brand-dot"></span>
      <span class="brand-name">Ward Compass</span>
    </div>
    <div class="contact-rule"></div>
    <div class="contact-info">
      <p class="person-name">Salwa Kettani</p>
      <p class="person-role">CEO</p>
      <p class="address">14 Annakhil 7<br>H.R.B. Rabat, Morocco</p>
      <p class="contact-line"><span class="label">P:</span>+90 612 348 2175</p>
      <p class="contact-line"><span class="label">E:</span>info@wardcompass.example</p>
      <p class="contact-line"><span class="label">W:</span>www.wardcompass.example</p>
    </div>
  </section>
</body>
</html>
```